Design a Website for an IT Support Company

We are an IT support company that provides commercial IT support and services to small and medium sized businesses. We are in need of a website to be developed for our business.
We would like to work with someone who is either familiar with the IT field, or has developed a website for an IT support company in the past.
Some examples of designs/layouts that we like:
https://www.veldaworks.example/
http://www.marsbyquill.example/
http://817kq.example/
http://www.olbenstructures.example/
http://www.bykq.example/
I have attached a word document that gives a menu system/page layout format that we would like for our website as well as branch office phone numbers. Our logo is also attached that you can use for your design purposes. We currently do not have copy produced for all of the pages outlined in the word document, but would get this done during the project with the selected designer.
We would like the website to be SEO friendly & fully responsive. We would prefer a Wordpress format, however, we are open to HTML formats as well.

```html
<!DOCTYPE html>
<html lang="en">
<head>
<meta charset="utf-8">
<title>Strideline IT – Commercial IT Support and Services</title>
<link href="https://fonts.googleapis.com/css2?family=Lato:wght@300;400;700&family=Mulish:wght@300;400;600;700&display=swap" rel="stylesheet">
<style>
:root{
  --blue:#1273b8;
  --blue-dark:#0d5f99;
  --ink:#333333;
  --muted:#8a8a8a;
  --grey-card:#8a8b8d;
  --black-card:#212121;
  --band:#ececec;
  --white:#ffffff;
  --line:#d4d4d4;
}
*{box-sizing:border-box;margin:0;padding:0}
html,body{width:1200px;height:2620px;overflow:hidden}
body{position:relative;background:var(--white);font-family:"Mulish",sans-serif;color:var(--ink)}
.abs{position:absolute}

/* header */
.site-header{position:absolute;left:0;top:0;width:1200px;height:110px;background:var(--white)}
.brand{position:absolute;left:119px;top:34px;display:flex;align-items:center;gap:12px}
.brand-dot{width:34px;height:34px;border-radius:50%;background:var(--blue)}
.brand-name{font-family:"Mulish",sans-serif;font-weight:700;font-size:30px;color:var(--ink);letter-spacing:.5px}
.main-nav a{position:absolute;top:62px;font-family:"Lato",sans-serif;font-size:16px;color:#555;text-decoration:none;letter-spacing:.5px}
.main-nav a.is-active{color:var(--blue);font-weight:700}
.nav-marker{position:absolute;left:582px;top:26px;width:14px;height:14px;border-radius:50%;background:var(--blue)}

/* hero */
.hero{position:absolute;left:0;top:110px;width:1200px;height:580px;background:linear-gradient(100deg,#3b4450 0%,#56606b 35%,#6d7580 60%,#8b96a3 100%)}
.hero-title{position:absolute;left:0;width:1200px;text-align:center;color:var(--white);font-family:"Lato",sans-serif;font-weight:300}
.hero-title.line-1{top:196px;font-size:35px}
.hero-title.line-2{top:236px;font-size:47px;font-weight:400}
.hero-btn{position:absolute;left:519px;top:313px;width:162px;height:42px;border:2px solid var(--white);border-radius:21px;background:var(--blue);color:var(--white);font-family:"Lato",sans-serif;font-size:17px;display:flex;align-items:center;padding-left:26px}
.hero-btn span.arrow{position:absolute;right:6px;top:5px;width:28px;height:28px;border-radius:50%;background:var(--white)}
.hero-chevron{position:absolute;left:582px;top:416px}
.slider-dots{position:absolute;left:529px;top:521px;display:flex;gap:10px}
.slider-dots i{display:block;width:26px;height:3px;background:var(--white)}

/* services */
.section-mark{position:absolute;left:585px;width:30px;height:30px;border-radius:50%;background:var(--blue)}
.section-title{position:absolute;left:0;width:1200px;text-align:center;font-size:32px;font-weight:400;color:var(--ink)}
.section-lead{position:absolute;left:240px;width:720px;text-align:center;font-size:14px;line-height:26px;color:#777}
.service-card{position:absolute;top:996px;width:304px;height:436px;color:var(--white)}
.service-card.data{left:117px;background:var(--grey-card)}
.service-card.cloud{left:442px;background:var(--blue)}
.service-card.voice{left:779px;background:var(--black-card)}
.card-icon{position:absolute;left:84px;top:-74px;width:136px;height:136px;border-radius:50%;background:var(--white);display:flex;align-items:center;justify-content:center}
.data .card-icon{border:3px solid var(--grey-card)}
.cloud .card-icon{border:3px solid var(--blue)}
.voice .card-icon{border:3px solid var(--black-card)}
.card-title{position:absolute;top:78px;width:100%;text-align:center;font-size:28px;font-weight:400}
.card-list{position:absolute;top:130px;width:100%;list-style:none;text-align:center;font-size:14.5px;line-height:29px}
.card-list li::before{content:"";display:inline-block;width:0;height:0;border-left:5px solid var(--white);border-top:4px solid transparent;border-bottom:4px solid transparent;margin-right:8px;vertical-align:1px}

/* why */
.why{position:absolute;left:0;top:1480px;width:1200px;height:538px;background:var(--band)}
.why-photo{position:absolute;left:140px;top:78px;width:393px;height:393px;border-radius:50%;background:radial-gradient(circle at 60% 45%,#d9cfc6 0%,#9da3a8 45%,#3e4247 100%)}
.why-title{position:absolute;left:558px;top:110px;font-size:33px;font-weight:400;color:var(--ink)}
.why-copy{position:absolute;left:562px;width:496px;font-size:14.5px;line-height:25px;color:var(--muted)}
.btn-read{position:absolute;left:562px;top:379px;width:135px;height:38px;background:var(--blue);color:var(--white);font-family:"Lato",sans-serif;font-size:15px;display:flex;align-items:center;justify-content:center;letter-spacing:.5px}

/* contact */
.contact{position:absolute;left:0;top:2018px;width:1200px;height:507px;background:linear-gradient(120deg,#e6e6e6 0%,#f4f4f4 40%,#efefef 70%,#dedede 100%)}
.contact-title{position:absolute;left:0;width:1200px;top:64px;text-align:center;font-size:37px;font-weight:400;color:var(--ink)}
.field{position:absolute;left:133px;width:426px;height:38px;background:var(--white);border:1px solid var(--line);font-size:14px;color:#666;padding:10px 14px}
.field.message{height:96px}
.btn-submit{position:absolute;left:135px;top:384px;width:134px;height:37px;background:var(--blue);color:var(--white);font-family:"Lato",sans-serif;font-size:16px;display:flex;align-items:center;justify-content:center;letter-spacing:.5px}
.contact-info{position:absolute;left:655px;top:150px;list-style:none}
.contact-info li{position:relative;height:33px;padding-left:28px;font-size:14.5px;color:#444;line-height:22px}
.contact-info svg{position:absolute;left:0;top:3px}

/* footer */
.site-footer{position:absolute;left:0;top:2525px;width:1200px;height:95px;background:var(--white)}
.copyright{position:absolute;left:121px;top:33px;font-size:14px;color:#555}
.social{position:absolute;left:931px;top:27px;display:flex;gap:6px}
.social i{display:block;width:32px;height:32px;border-radius:50%;border:2px solid var(--blue)}
</style>
</head>
<body>

<header class="site-header">
  <div class="brand"><span class="brand-dot"></span><span class="brand-name">Strideline IT</span></div>
  <span class="nav-marker"></span>
  <nav class="main-nav">
    <a class="is-active" href="#" style="left:568px">HOME</a>
    <a href="#" style="left:669px">SERVICES</a>
    <a href="#" style="left:797px">WHY STRIDELINE IT</a>
    <a href="#" style="left:985px">CONTACT</a>
  </nav>
</header>

<section class="hero" role="img" aria-label="Two IT technicians working at server racks in a data centre, one holding a laptop">
  <h1 class="hero-title line-1">IT Support company that Provides</h1>
  <h2 class="hero-title line-2">Commercial IT Support and Services</h2>
  <a class="hero-btn">Read More<span class="arrow"><svg width="28" height="28" viewBox="0 0 28 28"><path d="M12 9l5 5-5 5" fill="none" stroke="#1273b8" stroke-width="2.2"/></svg></span></a>
  <svg class="hero-chevron" width="36" height="22" viewBox="0 0 36 22"><path d="M3 4l15 14L33 4" fill="none" stroke="#fff" stroke-width="4"/></svg>
  <div class="slider-dots"><i></i><i></i><i></i></div>
</section>

<section class="services">
  <span class="section-mark" style="top:730px"></span>
  <h2 class="section-title" style="top:782px">Our Services</h2>
  <p class="section-lead" style="top:826px">interdum vel blandit sed nulla In ullamcorper est eget tempor cursus neque mi consectetuer mi a ultricies massa est sed nisl Class aptent taciti sociosqu ad litora torquent per conubia</p>

  <article class="service-card data">
    <div class="card-icon">
      <svg width="70" height="70" viewBox="0 0 70 70" fill="none" stroke="#8a8b8d" stroke-width="3">
        <ellipse cx="30" cy="14" rx="22" ry="8"/>
        <path d="M8 14v34c0 4 10 8 22 8M52 14v16M8 25c0 4 10 8 22 8s22-4 22-8M8 37c0 4 10 8 22 8"/>
        <circle cx="50" cy="50" r="13"/>
        <path d="M43 50l5 5 9-9"/>
      </svg>
    </div>
    <h3 class="card-title">Data</h3>
    <ul class="card-list">
      <li>Managed IT Services</li><li>IT Support &amp; Consulting</li><li>IT Helpdesk Services</li><li>Network Security</li><li>Data Backup &amp; Recovery</li><li>Servers &amp; Virtualization</li><li>Remote Monitoring Services</li><li>Wireless Networking</li><li>Email &amp; Spam Threat Management</li><li>Structured Cabling</li>
    </ul>
  </article>

  <article class="service-card cloud">
    <div class="card-icon">
      <svg width="80" height="70" viewBox="0 0 80 70" fill="none" stroke="#1273b8" stroke-width="3">
        <path d="M24 38h34a10 10 0 0 0 0-20 14 14 0 0 0-26-4 10 10 0 0 0-8 24z"/>
        <path d="M6 46h10l14 8h18a4 4 0 0 0 0-8H34M16 60h38l18-14a4 4 0 0 0-6-5l-14 9"/>
      </svg>
    </div>
    <h3 class="card-title">Cloud</h3>
    <ul class="card-list">
      <li>Nimbus Office Migrations</li><li>Corvane Cloud Management Services</li><li>Cloud Migration Services</li><li>Hosted Virtual Servers</li><li>Hosted Telephone Systems</li>
    </ul>
  </article>

  <article class="service-card voice">
    <div class="card-icon">
      <svg width="66" height="66" viewBox="0 0 66 66" fill="none" stroke="#212121" stroke-width="3.5">
        <path d="M10 40V32a23 23 0 0 1 46 0v8"/>
        <rect x="8" y="38" width="12" height="20" rx="5"/>
        <rect x="46" y="38" width="12" height="20" rx="5"/>
      </svg>
    </div>
    <h3 class="card-title">Voice</h3>
    <ul class="card-list">
      <li>Tollway PBX Consulting</li><li>Business Telephone Systems</li><li>Multiple Office Phone Systems</li><li>Brightline Telephone Systems</li><li>SIP Trunks</li>
    </ul>
  </article>
</section>

<section class="why">
  <div class="why-photo" role="img" aria-label="Support agent wearing a headset at a desk in a busy help centre"></div>
  <h2 class="why-title">Why Strideline IT</h2>
  <p class="why-copy" style="top:172px">Praesent sit amet est In dictum dolor eu dictum porttitor enim felis viverra mi eget luctus massa purus quis odio Etiam nulla massa pharetra facilisis volutpat in imperdiet sit amet sem Aliquam nec erat at purus cursus interdum Vestibulum ligula augue bibendum accumsan</p>
  <p class="why-copy" style="top:285px">vestibulum ut commodo a mi Morbi ornare gravida elit Integer congue augue et malesuada iaculis ipsum dui aliquet felis at cursus magna nisl nec elit Donec iaculis diam a nisi accumsan</p>
  <a class="btn-read">READ MORE</a>
</section>

<section class="contact" role="img" aria-label="Soft grey desk scene with keyboard, notebook and pen">
  <h2 class="contact-title">Contact Us</h2>
  <div class="field" style="top:140px">First Name</div>
  <div class="field" style="top:185px">Email address</div>
  <div class="field" style="top:232px">Phone</div>
  <div class="field message" style="top:278px">Message</div>
  <a class="btn-submit">SUBMIT</a>
  <ul class="contact-info">
    <li><svg width="14" height="18" viewBox="0 0 14 18"><path d="M7 1a6 6 0 0 0-6 6c0 4 6 10 6 10s6-6 6-10a6 6 0 0 0-6-6z" fill="#1273b8"/><circle cx="7" cy="7" r="2.2" fill="#fff"/></svg>4820 Larkspur Avenue #GA Texas 75201 TX</li>
    <li><svg width="16" height="14" viewBox="0 0 16 14"><rect x="1" y="2" width="14" height="10" fill="none" stroke="#1273b8" stroke-width="1.5"/><path d="M1 2l7 6 7-6" fill="none" stroke="#1273b8" stroke-width="1.5"/></svg>info@companyname.com</li>
    <li><svg width="16" height="16" viewBox="0 0 16 16"><path d="M3 1l3 3-2 2a9 9 0 0 0 6 6l2-2 3 3-2 2C7 15 1 9 1 3z" fill="none" stroke="#1273b8" stroke-width="1.5"/></svg>Main Number: 972-555-0160</li>
    <li>Houston: 832-555-0142</li>
    <li>San Antonio: 210-555-0187</li>
    <li>Austin: 512-555-0119</li>
    <li>Tulsa: 918-555-0173</li>
    <li>Oklahoma City: 405-555-0128</li>
  </ul>
</section>

<footer class="site-footer">
  <p class="copyright">© 2017 Company Name&nbsp; All right reserved&nbsp; Term of Use</p>
  <div class="social"><i></i><i></i><i></i><i></i></div>
</footer>

</body>
</html>
```